E-learning Information & Community Website Needs a Makeover

I'm looking for a design makeover for my website "Tavipor.club". Tavipor's aim is to connect people to online learning through forums, information, guides & independent reviews. The site was launched in September 2014 using a forum software (Xenforo), but now needs a more polished and sophisticated look which communicates expertise and professionalism. I would like to see designs that use the current "Tavipor" blue (#0070c0). To visit the current website, go to http://www.tavipor.club/

Target Market(s)

People wishing to study online

Industry/Entity Type

Club

Number of Pages Required

4 page

Font styles to use
Sans Serif

Requirements
Must have
• A simple, clear and sophisticated lading page with links to the site's key features: discussion forums, Useful resources, Reviews, News etc, Articles. (See layout idea file attached)
• The main pages are the Landing Page, Discussion Forums, Resources & Reviews
• I would like to see designs that use the current "Tavipor" blue (#0070c0).
Nice to have
• Something uncluttered and easy to understand. The design should convey expertise in the field of online learning, giving users a sense of trust in the site's offerings.
• To give an idea of the sort of thing I'm after, take a look at wendricast.com website (screenshot attached)

```html
<!DOCTYPE html>
<html lang="en">
<head>
<meta charset="utf-8">
<title>Tavipor – Connecting People to Online Learning</title>
<link href="https://fonts.googleapis.com/css2?family=Open+Sans:ital,wght@0,300;0,400;0,600;0,700;0,800;1,400&display=swap" rel="stylesheet">
<style>
:root{
  --brand:#0070c0;
  --brand-light:#3a9ff0;
  --brand-mid:#1f86d8;
  --accent:#e0650f;
  --ink:#444;
  --muted:#777;
  --row-alt:#e9e9e9;
  --line:#d8d8d8;
  --footer:#3b3b3b;
  --white:#fff;
}
*{box-sizing:border-box;margin:0;padding:0}
html,body{width:1200px;height:2703px;overflow:hidden}
body{position:relative;font-family:"Open Sans",Arial,sans-serif;color:var(--ink);background:var(--white)}

/* top bar */
.topbar{position:absolute;left:0;top:0;width:1200px;height:76px;background:var(--brand)}
.brand{position:absolute;left:99px;top:12px;color:var(--white)}
.brand-name{font-size:28px;font-weight:400;line-height:32px}
.brand-tag{font-size:12px;font-weight:600;line-height:16px}
.social{position:absolute;left:508px;top:28px;display:flex;align-items:center;gap:18px;color:var(--white);font-size:11px;font-weight:600}
.social .dot{width:10px;height:10px;border-radius:50%;background:var(--white);opacity:.9}
.lang{position:absolute;left:829px;top:21px;width:108px;height:36px;background:#0a5fa3;color:var(--white);font-size:11px;display:flex;align-items:center;padding-left:12px;gap:10px}
.lang .flag{width:16px;height:11px;background:#c9d6ea}
.lang svg{position:absolute;right:12px;top:15px}
.signin{position:absolute;left:950px;top:20px;width:151px;height:38px;background:var(--brand-light);color:var(--white);font-size:13px;display:flex;align-items:center;justify-content:center;border-radius:2px}

/* hero */
.hero{position:absolute;left:0;top:76px;width:1200px;height:699px;overflow:hidden}
.hero-photo{position:absolute;inset:0;background:radial-gradient(ellipse at 50% 30%,#5a6470 0%,#353c45 45%,#1e2329 100%)}
.nav{position:absolute;left:0;top:56px;width:1200px;height:20px}
.nav a{position:absolute;color:var(--white);font-size:13px;font-weight:700;text-decoration:none;letter-spacing:.2px}
.hero-kicker{position:absolute;left:0;top:224px;width:1200px;text-align:center;color:var(--white);font-size:27px;font-weight:300}
.hero-title{position:absolute;left:0;top:262px;width:1200px;text-align:center;color:var(--white);font-size:36px;font-weight:700;letter-spacing:.5px}
.hero-cta{position:absolute;left:512px;top:331px;width:174px;height:49px;background:var(--brand-mid);color:var(--white);font-size:13px;display:flex;align-items:center;justify-content:center;border-radius:2px}
.feature{position:absolute;width:190px;height:57px;border:1.5px solid rgba(255,255,255,.85);border-radius:3px;color:var(--white);font-size:13px;display:flex;align-items:center;justify-content:center;background:rgba(0,0,0,.15)}

/* section headings */
.section-title{position:absolute;left:99px;color:var(--brand);font-size:26px;font-weight:800;letter-spacing:.2px}
.section-title span{font-weight:400;color:#555;font-size:21px}

/* threads table */
.threads{position:absolute;left:99px;top:892px;width:1002px;border:1px solid var(--line)}
.threads-head{display:flex;height:47px;background:var(--brand);color:var(--white);font-size:12px;font-weight:700}
.threads-head div{display:flex;align-items:center;padding-left:22px;border-right:1px solid rgba(255,255,255,.25)}
.thread{display:flex;height:69.5px;background:var(--white);font-size:12px}
.thread:nth-child(odd){background:var(--row-alt)}
.cell{border-right:1px solid var(--line);padding:16px 0 0 22px;line-height:21px}
.cell:last-child,.threads-head div:last-child{border-right:none}
.c1{width:405px;position:relative;padding-left:78px}
.c2,.c3,.c4{width:139px}
.c5{width:180px}
.avatar{position:absolute;left:12px;top:10px;width:50px;height:50px;background:linear-gradient(135deg,#b9a595,#6b5a50)}
.cat{color:var(--accent);font-weight:700}
.sub{color:var(--brand-mid)}
.meta{color:var(--muted);font-size:11px}
.strong{color:#555;font-weight:600}
.user{color:var(--brand-mid)}

.more{position:absolute;left:490px;width:220px;height:54px;background:var(--brand-mid);color:var(--white);font-size:13px;display:flex;align-items:center;justify-content:center;border-radius:2px;box-shadow:0 8px 6px -5px rgba(0,0,0,.35)}

/* activity feed */
.feed{position:absolute;left:99px;top:1712px;width:1002px;border:1px solid var(--line)}
.post{position:relative;height:120.7px;background:var(--white);padding:14px 20px 0 83px;font-size:11px;line-height:20px;border-bottom:1px solid var(--line)}
.post:nth-child(odd){background:var(--row-alt)}
.post:last-child{border-bottom:none}
.post .avatar{left:18px;top:14px;width:50px;height:42px}
.post-user{color:var(--brand-mid);font-weight:700;font-size:12px}
.post-action{color:var(--muted)}
.post-excerpt{color:var(--muted);white-space:nowrap;overflow:hidden;text-overflow:ellipsis}
.post-time{color:var(--accent);font-style:italic;font-size:10px}

/* footer */
.footer{position:absolute;left:0;top:2622px;width:1200px;height:81px;background:var(--footer);color:#bbb;font-size:11px}
.footer-links{position:absolute;left:99px;top:32px;display:flex;gap:18px}
.footer-copy{position:absolute;left:912px;top:32px}
.footer-code{position:absolute;left:1152px;top:32px}
</style>
</head>
<body>

<header class="topbar">
  <div class="brand">
    <div class="brand-name">Tavipor</div>
    <div class="brand-tag">Connecting People to Online Learning</div>
  </div>
  <div class="social">Connect with our social network :
    <span class="dot"></span><span class="dot"></span><span class="dot"></span><span class="dot"></span>
  </div>
  <div class="lang"><span class="flag"></span>English
    <svg width="8" height="5" viewBox="0 0 8 5"><path d="M0 0h8L4 5z" fill="#fff"/></svg>
  </div>
  <div class="signin">Sign in or Signup</div>
</header>

<section class="hero">
  <div class="hero-photo" role="img" aria-label="Photo of business people walking in a bright modern glass building"></div>
  <nav class="nav">
    <a style="left:148px">HOME</a>
    <a style="left:243px">FORUMS</a>
    <a style="left:355px">RESOURCES</a>
    <a style="left:485px">MEMBERS</a>
    <a style="left:605px">FAQ</a>
    <a style="left:688px">BLOG</a>
    <a style="left:780px">TAVIPOR ESPAÑOL</a>
    <a style="left:964px">MOOC SCOOP</a>
  </nav>
  <div class="hero-kicker">AT THE HEART OF CONNECTING PEOPLE TO</div>
  <div class="hero-title">ONLINE LEARNING</div>
  <div class="hero-cta">SIGNUP FOR FREE</div>
  <div class="feature" style="left:274px;top:457px">GETTING STARTED</div>
  <div class="feature" style="left:504px;top:457px">DISCUSSIONS</div>
  <div class="feature" style="left:735px;top:457px">REVIEWS</div>
  <div class="feature" style="left:274px;top:543px">TIPS &amp; GUIDELINES</div>
  <div class="feature" style="left:504px;top:543px">NEWS &amp; ARTICLES</div>
  <div class="feature" style="left:735px;top:543px">NEWSLETTER</div>
</section>

<h2 class="section-title" style="top:826px">TAVIPOR - <span>CONNECTING PEOPLE TO ONLINE LEARNING</span></h2>

<div class="threads">
  <div class="threads-head">
    <div class="c1" style="padding-left:22px">RECENT THREADS</div>
    <div class="c2">START DATE</div>
    <div class="c3">REPLIES</div>
    <div class="c4">VIEWS</div>
    <div class="c5">LAST MESSAGE</div>
  </div>
  <div class="thread"><div class="cell c1"><div class="avatar" role="img" aria-label="Member avatar photo"></div><span class="cat">COURSES</span> - <span class="sub">Corvane MOOCs</span><br><span class="meta">Carolyn, Today at 9:30 AM, Lernio</span></div><div class="cell c2"><span class="strong">On</span><br><span class="meta">27 March 2015</span></div><div class="cell c3"><span class="strong">Replies</span><br><span class="meta">Views :</span></div><div class="cell c4"><span class="strong">0</span><br><span class="meta">42</span></div><div class="cell c5"><span class="user">Carolyn</span><br><span class="meta">Today at 9:30 AM</span></div></div>
  <div class="thread"><div class="cell c1"><div class="avatar" role="img" aria-label="Member avatar photo"></div><span class="cat">NEWS</span> - <span class="sub">Corvane MOOCs</span><br><span class="meta">Carolyn, Today at 9:30 AM, Lernio</span></div><div class="cell c2"><span class="strong">On</span><br><span class="meta">27 March 2015</span></div><div class="cell c3"><span class="strong">Replies</span><br><span class="meta">Views :</span></div><div class="cell c4"><span class="strong">0</span><br><span class="meta">42</span></div><div class="cell c5"><span class="user">Carolyn</span><br><span class="meta">Today at 9:30 AM</span></div></div>
  <div class="thread"><div class="cell c1"><div class="avatar" role="img" aria-label="Member avatar photo"></div><span class="cat">COURSES</span> - <span class="sub">Corvane MOOCs</span><br><span class="meta">Carolyn, Today at 9:30 AM, Lernio</span></div><div class="cell c2"><span class="strong">On</span><br><span class="meta">27 March 2015</span></div><div class="cell c3"><span class="strong">Replies</span><br><span class="meta">Views :</span></div><div class="cell c4"><span class="strong">0</span><br><span class="meta">42</span></div><div class="cell c5"><span class="user">Carolyn</span><br><span class="meta">Today at 9:30 AM</span></div></div>
  <div class="thread"><div class="cell c1"><div class="avatar" role="img" aria-label="Member avatar photo"></div><span class="cat">REVIEWS</span> - <span class="sub">Corvane MOOCs</span><br><span class="meta">Carolyn, Today at 9:30 AM, Lernio</span></div><div class="cell c2"><span class="strong">On</span><br><span class="meta">27 March 2015</span></div><div class="cell c3"><span class="strong">Replies</span><br><span class="meta">Views :</span></div><div class="cell c4"><span class="strong">0</span><br><span class="meta">42</span></div><div class="cell c5"><span class="user">Carolyn</span><br><span class="meta">Today at 9:30 AM</span></div></div>
  <div class="thread"><div class="cell c1"><div class="avatar" role="img" aria-label="Member avatar photo"></div><span class="cat">EVENT</span> - <span class="sub">Corvane MOOCs</span><br><span class="meta">Carolyn, Today at 9:30 AM, Lernio</span></div><div class="cell c2"><span class="strong">On</span><br><span class="meta">27 March 2015</span></div><div class="cell c3"><span class="strong">Replies</span><br><span class="meta">Views :</span></div><div class="cell c4"><span class="strong">0</span><br><span class="meta">42</span></div><div class="cell c5"><span class="user">Carolyn</span><br><span class="meta">Today at 9:30 AM</span></div></div>
  <div class="thread"><div class="cell c1"><div class="avatar" role="img" aria-label="Member avatar photo"></div><span class="cat">COURSES</span> - <span class="sub">Corvane MOOCs</span><br><span class="meta">Carolyn, Today at 9:30 AM, Lernio</span></div><div class="cell c2"><span class="strong">On</span><br><span class="meta">27 March 2015</span></div><div class="cell c3"><span class="strong">Replies</span><br><span class="meta">Views :</span></div><div class="cell c4"><span class="strong">0</span><br><span class="meta">42</span></div><div class="cell c5"><span class="user">Carolyn</span><br><span class="meta">Today at 9:30 AM</span></div></div>
  <div class="thread"><div class="cell c1"><div class="avatar" role="img" aria-label="Member avatar photo"></div><span class="cat">EVENT</span> - <span class="sub">Corvane MOOCs</span><br><span class="meta">Carolyn, Today at 9:30 AM, Lernio</span></div><div class="cell c2"><span class="strong">On</span><br><span class="meta">27 March 2015</span></div><div class="cell c3"><span class="strong">Replies</span><br><span class="meta">Views :</span></div><div class="cell c4"><span class="strong">0</span><br><span class="meta">42</span></div><div class="cell c5"><span class="user">Carolyn</span><br><span class="meta">Today at 9:30 AM</span></div></div>
  <div class="thread"><div class="cell c1"><div class="avatar" role="img" aria-label="Member avatar photo"></div><span class="cat">COURSES</span> - <span class="sub">Corvane MOOCs</span><br><span class="meta">Carolyn, Today at 9:30 AM, Lernio</span></div><div class="cell c2"><span class="strong">On</span><br><span class="meta">27 March 2015</span></div><div class="cell c3"><span class="strong">Replies</span><br><span class="meta">Views :</span></div><div class="cell c4"><span class="strong">0</span><br><span class="meta">42</span></div><div class="cell c5"><span class="user">Carolyn</span><br><span class="meta">Today at 9:30 AM</span></div></div>
</div>

<div class="more" style="top:1535px">Click here for view more</div>

<h2 class="section-title" style="top:1645px">FROM THE COMMUNITY <span>RECENT THREADS/ACTIVITY</span></h2>

<div class="feed">
  <div class="post"><div class="avatar" role="img" aria-label="Member avatar photo"></div><span class="post-user">CAROLYN</span> <span class="post-action">posted a new thread.</span><br><span class="cat">COURSES</span> - <span class="sub">Corvane MOOCs</span><div class="post-excerpt">Lorem Ipsum is simply dummy text of the printing and typesetting industry. Lorem Ipsum has been the industry's standard dummy text ever since the 1500s unknown...</div><div class="post-time">Yesterday at 2:49 PM</div></div>
  <div class="post"><div class="avatar" role="img" aria-label="Member avatar photo"></div><span class="post-user">CAROLYN</span> <span class="post-action">posted a new thread.</span><br><span class="cat">COURSES</span> - <span class="sub">Corvane MOOCs</span><div class="post-excerpt">Lorem Ipsum is simply dummy text of the printing and typesetting industry. Lorem Ipsum has been the industry's standard dummy text ever since the 1500s unknown...</div><div class="post-time">Yesterday at 2:49 PM</div></div>
  <div class="post"><div class="avatar" role="img" aria-label="Member avatar photo"></div><span class="post-user">CAROLYN</span> <span class="post-action">posted a new thread.</span><br><span class="cat">COURSES</span> - <span class="sub">Corvane MOOCs</span><div class="post-excerpt">Lorem Ipsum is simply dummy text of the printing and typesetting industry. Lorem Ipsum has been the industry's standard dummy text ever since the 1500s unknown...</div><div class="post-time">Yesterday at 2:49 PM</div></div>
  <div class="post"><div class="avatar" role="img" aria-label="Member avatar photo"></div><span class="post-user">CAROLYN</span> <span class="post-action">posted a new thread.</span><br><span class="cat">COURSES</span> - <span class="sub">Corvane MOOCs</span><div class="post-excerpt">Lorem Ipsum is simply dummy text of the printing and typesetting industry. Lorem Ipsum has been the industry's standard dummy text ever since the 1500s unknown...</div><div class="post-time">Yesterday at 2:49 PM</div></div>
  <div class="post"><div class="avatar" role="img" aria-label="Member avatar photo"></div><span class="post-user">CAROLYN</span> <span class="post-action">posted a new thread.</span><br><span class="cat">COURSES</span> - <span class="sub">Corvane MOOCs</span><div class="post-excerpt">Lorem Ipsum is simply dummy text of the printing and typesetting industry. Lorem Ipsum has been the industry's standard dummy text ever since the 1500s unknown...</div><div class="post-time">Yesterday at 2:49 PM</div></div>
  <div class="post"><div class="avatar" role="img" aria-label="Member avatar photo"></div><span class="post-user">CAROLYN</span> <span class="post-action">posted a new thread.</span><br><span class="cat">COURSES</span> - <span class="sub">Corvane MOOCs</span><div class="post-excerpt">Lorem Ipsum is simply dummy text of the printing and typesetting industry. Lorem Ipsum has been the industry's standard dummy text ever since the 1500s unknown...</div><div class="post-time">Yesterday at 2:49 PM</div></div>
</div>

<div class="more" style="top:2477px">Click here for view more</div>

<footer class="footer">
  <div class="footer-links"><span>Home</span><span>/</span><span>About</span><span>/</span><span>Contact Us</span><span>/</span><span>Help</span><span>/</span><span>FAQ</span><span>/</span><span>Community Guidelines</span></div>
  <div class="footer-copy">© 2015. Tavipor. All rights reserved.</div>
  <div class="footer-code">C8</div>
</footer>

</body>
</html>
```